New template needed for Joomla 3.2 website

We are a mortgage origination company based in Johannesburg, South Africa and require a sleek, modern & professional look for our website.
The website is complete and your template should accommodate all pages on the site (there are not many) and be ready for Joomla implementation.
Our website can be viewed at www.keystonebondhub.co.za
Target Market(s)
We are targeting consumers who require mortgage finance to buy real estate. There is no particular demographic, except that we cater to South African home buyers exclusively!
Requirements
Must have
- It must look professional and modern.
Take a look at competitor websites:
www.ziva.co.za
www.pkbondfinder.com
http://www.tallwavegroup.co.za/bondpeak/
http://www.ridgeloan.co.za/
We want to beat the competition !!
Nice to have
- Website should blend with company logo and play on the symbol in the logo.
I want more of a people / photo element to the template. It needs to make us seem "tangible"

```html
<!DOCTYPE html>
<html lang="en">
<head>
<meta charset="utf-8">
<title>Keystone Bond Hub</title>
<link href="https://fonts.googleapis.com/css2?family=PT+Sans+Narrow&family=Arimo:wght@400;700&display=swap" rel="stylesheet">
<style>
:root{
  --blue:#2f78bd;
  --blue-dark:#1c5ba6;
  --title:#1f6bb3;
  --text:#6b6b6b;
  --line:#cfcfcf;
  --white:#ffffff;
}
*{margin:0;padding:0;box-sizing:border-box}
html,body{width:864px;height:1200px;overflow:hidden;background:var(--white)}
body{position:relative;font-family:"Arimo",Arial,sans-serif;color:var(--text)}
.abs{position:absolute}
.heading{font-family:"PT Sans Narrow",sans-serif;color:var(--title);font-weight:400}

.brand{left:94px;top:18px;font-family:"Arimo",sans-serif;font-weight:400;font-size:17px;color:var(--title);line-height:1}
.call{right:96px;top:16px;font-size:13px;color:var(--title)}

.nav{left:94px;top:55px;width:770px;height:50px;background:var(--blue);display:flex}
.nav a{color:var(--white);text-decoration:none;font-size:10px;line-height:50px;padding:0 15.5px}
.nav a.active{background:var(--blue-dark)}

.hero{left:94px;top:105px;width:676px;height:320px;background:linear-gradient(120deg,#cfd5dc 0%,#8b8e92 45%,#b7b1ab 70%,#e4e6e8 100%)}
.hero-caption{left:94px;top:347px;width:485px;height:78px;background:rgba(30,30,30,.85);color:var(--white);font-family:"PT Sans Narrow",sans-serif;font-size:31px;line-height:78px;padding-left:32px}
.hero-arrow{top:211px;width:34px;height:32px;background:rgba(120,120,120,.55)}
.hero-arrow svg{display:block;margin:8px auto}

.promo-title{font-size:20px;top:449px}
.promo-img{top:486px;width:112px;height:110px;border:1px solid #e2e2e2;box-shadow:0 1px 3px rgba(0,0,0,.15)}
.promo-text{top:484px;font-size:10.4px;line-height:17.6px}

.feature{width:176px;text-align:center}
.feature h3{font-size:16.5px;line-height:20px}
.feature .ring{width:54px;height:54px;border:1px solid #555;border-radius:50%;margin:14px auto 0;display:flex;align-items:center;justify-content:center}
.feature p{font-size:10.4px;line-height:17.6px;margin:14px auto 0;height:53px;width:134px}
.btn{display:block;width:86px;height:29px;margin:11px auto 0;background:var(--blue);color:var(--white);font-size:12.5px;line-height:29px;text-decoration:none}

.card{top:854px;width:217px;height:188px;border:1px solid var(--line);text-align:center}
.card .icon{width:40px;height:40px;margin:20px auto 0}
.card h3{font-size:16.5px;margin-top:9px}
.card p{font-size:10.2px;line-height:17.6px;margin-top:6px;padding:0 18px}

.footer{left:0;top:1074px;width:864px;height:126px;background:var(--blue);color:var(--white);text-align:center}
.footer-links{font-size:10.4px;margin-top:21px}
.footer-links span{margin:0 8px}
.copy{font-size:10.4px;margin-top:14px}
.social{display:flex;justify-content:center;gap:12px;margin-top:14px}
.social i{width:28px;height:28px;border:1.5px solid var(--white);border-radius:50%}
</style>
</head>
<body>

<header>
  <div class="abs brand">Keystone Bond Hub</div>
  <div class="abs call">Call Us : ( 010 ) 482 7315</div>
  <nav class="abs nav">
    <a class="active" href="#">HOME</a>
    <a href="#">ABOUT KEYSTONE</a>
    <a href="#">IMPORTANT INFORMATION</a>
    <a href="#">HOMELOAN CALCULATORS</a>
    <a href="#">APPLY ONLINE</a>
    <a href="#">CONTACT KEYSTONE</a>
  </nav>
</header>

<section>
  <div class="abs hero" role="img" aria-label="Photo of a smiling young couple signing home loan papers with a consultant"></div>
  <div class="abs hero-caption">FAST HOME LOANS. GREAT SERVICE !</div>
  <div class="abs hero-arrow" style="left:94px"><svg width="12" height="16" viewBox="0 0 12 16"><path d="M9 2 3 8l6 6" fill="none" stroke="#fff" stroke-width="2.2"/></svg></div>
  <div class="abs hero-arrow" style="left:736px"><svg width="12" height="16" viewBox="0 0 12 16"><path d="M3 2l6 6-6 6" fill="none" stroke="#fff" stroke-width="2.2"/></svg></div>
</section>

<section>
  <h2 class="abs heading promo-title" style="left:94px">Keystone Lead Referral Program</h2>
  <div class="abs promo-img" style="left:94px;background:linear-gradient(135deg,#f4f4f4,#e6e9ee 50%,#d7dfe9)" role="img" aria-label="Illustration of a red magnet attracting blue figures"></div>
  <p class="abs promo-text" style="left:218px;width:205px">We invite members of the public, estate agents, attorneys, property developers and all other property professionals to refer leads to us. Why not join our referal program and earn money for every successful lead. It pays!</p>

  <h2 class="abs heading promo-title" style="left:443px">Keystone Card</h2>
  <div class="abs promo-img" style="left:443px;background:linear-gradient(160deg,#e9f4fb,#49a9e0 45%,#1d5c9c)" role="img" aria-label="Illustration of two blue payment cards"></div>
  <p class="abs promo-text" style="left:566px;width:204px">All members of our lead referal program will receive an Keystone Homeloans card. We will load money earned from referals to your card and for you to spend in any way you please! These cards are accepted in all retail stores and restaurants.</p>
</section>

<section>
  <div class="abs feature" style="left:71px;top:620px">
    <h3 class="heading">Referral Program</h3>
    <div class="ring"><svg width="28" height="28" viewBox="0 0 28 28" fill="none" stroke="#333" stroke-width="2"><path d="M14 3 25 14 14 25"/><path d="M4 14h16M15 9l5 5-5 5"/></svg></div>
    <p>Click on the button below to join our lead referal program and start earning money.</p>
    <a class="btn" href="#">Join Today</a>
  </div>
  <div class="abs feature" style="left:253px;top:620px">
    <h3 class="heading">Get Pre Qualified</h3>
    <div class="ring"><svg width="26" height="30" viewBox="0 0 26 30" fill="none" stroke="#333" stroke-width="1.6"><path d="M4 2h14l4 4v18H4z"/><path d="M8 9h10M8 13h10M8 17h6"/><circle cx="19" cy="24" r="3.5"/></svg></div>
    <p>Our experienced consultants would be happy to prequalify you for a homeloan.</p>
    <a class="btn" href="#">Apply Now</a>
  </div>
  <div class="abs feature" style="left:438px;top:620px">
    <h3 class="heading">Ask a Question</h3>
    <div class="ring"><span style="font:700 34px Arimo,sans-serif;color:#333">?</span></div>
    <p>Ask an experienced consultant to answer all your questions about homeloan.</p>
    <a class="btn" href="#">Ask Now</a>
  </div>
  <div class="abs feature" style="left:614px;top:620px">
    <h3 class="heading">Calculators</h3>
    <div class="ring"><svg width="22" height="30" viewBox="0 0 22 30" fill="none" stroke="#333" stroke-width="1.8"><rect x="2" y="2" width="18" height="26" rx="2"/><rect x="5" y="5" width="12" height="6"/><path d="M6 15h2M10 15h2M14 15h2M6 19h2M10 19h2M14 19h2M6 23h2M10 23h2M14 23h2"/></svg></div>
    <p>Find out what you can afford with our convenient finance calculators.</p>
    <a class="btn" href="#">Calculate</a>
  </div>
</section>

<section>
  <div class="abs card" style="left:94px">
    <div class="icon" style="background:linear-gradient(#c9c4b7,#8f8a7e);border-radius:3px" role="img" aria-label="Small illustration of a bank building"></div>
    <h3 class="heading">100 % Free Of Charge</h3>
    <p>No hidden costs or service charges. Our fee is not hidden within the finance charges of your homeloan. We guarantee a 100% free of charge.</p>
  </div>
  <div class="abs card" style="left:324px">
    <div class="icon" style="background:radial-gradient(#f7d64a,#d99c12);border-radius:50%"></div>
    <h3 class="heading">Exceptional service</h3>
    <p>We guarantee a first class service to you. Our home loan specialists are up to date with the latest finance criteria from all the major financial.</p>
  </div>
  <div class="abs card" style="left:553px">
    <div class="icon" style="background:linear-gradient(#4b8fe0,#1b4fae);border-radius:3px" role="img" aria-label="Small illustration of a blue debt card"></div>
    <h3 class="heading">Credit Help</h3>
    <p>We guarantee a first class service to you. Our home loan specialists are up to date with the latest finance criteria from all the major financial.</p>
  </div>
</section>

<footer class="abs footer">
  <div class="footer-links">Privacy Policy<span>I</span>About Keystone<span>I</span>Contact Keystone</div>
  <div class="copy">Copyright © 2014 Keystone Bond Hub (Pty) Ltd</div>
  <div class="social"><i></i><i></i><i></i></div>
</footer>

</body>
</html>
```